International business needs business cards

Our company, DRV Ventures Inc. is in the business of supplying a range construction products with particular emphasis on CEMENT. We have developed our own brand - TORVAN SUPPLIES - with which to infiltrate the market. We are launching our brand of cement (TORVAN Type IS Cement) into the Caribbean which is unlike anything this market has ever seen. A monopoly has existed here for the past 60-odd years and the market has now opened to allow the importation of other brands and consumers are anxious and ready for change/improvement. We are very excited to be launching and want to make a great first impression. We will be conducting workshops and seminars (from government level to the hardware store owners) and we want our business card to give us the strong, confident introduction that we need.

Target Market(s)

construction; builders; engineers; home owners

Industry/Entity Type

Construction

Contact Information for Business Card

Marisol Depree
CEO
cell # 1 555 4180736
Ground floor,Lindell Plaza Suite 2734
George Town,Grand Cayman
Cayman Islands,KY1-4823
EMAIL: m.depree@drvventuresinc.example
web site drvventuresinc.example

COMPANY: skype info drv.ventures.example

second card
Yvette Brannock-Depree
CFO
CELL# 1 555 607 3941
George Town,Grand Cayman
Cayman Islands,KY1-4823
EMAIL: y.brannockdepree@drvventuresinc.example
website drvventuresinc.example

Requirements
Must have
• Business cards must display BOTH logos - DRV is the company and TORVAN is the brand.

```html
<!DOCTYPE html>
<html lang="en">
<head>
<meta charset="utf-8">
<title>DRV Ventures Inc. — Business Card</title>
<link rel="stylesheet" href="https://fonts.googleapis.com/css2?family=Open+Sans:wght@400;600;700;800&display=swap">
<style>
  :root {
    --bg: #2a2a2a;
    --card-white: #ffffff;
    --card-black: #050505;
    --ink: #1a1a1a;
    --accent-red: #8e1b1f;
    --icon-red: #b3242a;
    --grey: #4a4a4a;
  }
  * { box-sizing: border-box; margin: 0; padding: 0; }
  html, body {
    width: 1200px; height: 900px; overflow: hidden;
    background: var(--bg);
    font-family: "Open Sans", Arial, sans-serif;
  }
  .canvas {
    width: 1200px; height: 900px;
    display: flex; flex-direction: column; align-items: center; justify-content: center;
    gap: 40px;
  }
  .card {
    position: relative;
    width: 700px; height: 400px;
    border-radius: 24px;
    overflow: hidden;
    background: var(--card-white);
  }

  /* Back side: brand mark */
  .card-back { display: flex; flex-direction: column; align-items: center; justify-content: center; }
  .brand-mark { display: flex; align-items: center; gap: 16px; margin-bottom: 60px; }
  .brand-mark__dot { width: 30px; height: 30px; border-radius: 50%; background: var(--ink); }
  .brand-mark__name {
    font-size: 56px; font-weight: 700; letter-spacing: 6px; color: var(--ink);
  }
  .handle-line {
    position: absolute; right: 150px; bottom: 62px;
    display: flex; align-items: center; gap: 8px;
    font-size: 17px; font-weight: 600; color: var(--ink);
  }
  .handle-line__dot { width: 14px; height: 14px; border-radius: 50%; background: var(--icon-red); }

  /* Front side: contact */
  .card-front__panel { position: absolute; inset: 0; }
  .company-mark {
    position: absolute; left: 48px; top: 232px;
    display: flex; align-items: center; gap: 12px;
  }
  .company-mark__square { width: 52px; height: 52px; background: var(--accent-red); }
  .company-mark__name { font-size: 24px; font-weight: 700; color: #ffffff; }

  .contact {
    position: absolute; left: 402px; top: 78px; right: 24px;
    color: var(--ink);
  }
  .contact__name { font-size: 27px; font-weight: 800; letter-spacing: 0.3px; line-height: 1.1; }
  .contact__role { font-size: 14px; font-weight: 600; color: var(--accent-red); margin-top: 2px; }
  .contact__address { font-size: 14px; font-weight: 600; line-height: 1.35; margin-top: 16px; color: var(--grey); }
  .contact__list { list-style: none; margin-top: 20px; }
  .contact__item {
    display: flex; align-items: center; gap: 8px;
    font-size: 14px; font-weight: 600; line-height: 1.5; color: var(--ink);
  }
  .contact__icon { width: 12px; height: 12px; flex: none; }
</style>
</head>
<body>
<main class="canvas">

  <section class="card card-back" aria-label="Business card back">
    <div class="brand-mark">
      <span class="brand-mark__dot"></span>
      <span class="brand-mark__name">TORVAN</span>
    </div>
    <div class="handle-line">
      <span class="handle-line__dot"></span>
      <span>drv.ventures.example</span>
    </div>
  </section>

  <section class="card card-front" aria-label="Business card front">
    <svg class="card-front__panel" width="700" height="400" viewBox="0 0 700 400" aria-hidden="true">
      <path d="M0,0 H310 Q410,150 392,400 H0 Z" fill="var(--card-black)"/>
      <path d="M318,0 Q420,150 402,400" fill="none" stroke="var(--card-black)" stroke-width="2"/>
    </svg>

    <div class="company-mark">
      <span class="company-mark__square"></span>
      <span class="company-mark__name">DRV Ventures Inc.</span>
    </div>

    <div class="contact">
      <h1 class="contact__name">MARISOL DEPREE</h1>
      <p class="contact__role">CEO</p>
      <p class="contact__address">
        Ground floor,Lindell Plaza Suite 2734<br>
        George Town,Grand Cayman<br>
        Cayman Islands,KY1-4823
      </p>
      <ul class="contact__list">
        <li class="contact__item">
          <svg class="contact__icon" viewBox="0 0 12 12" aria-hidden="true"><path d="M2.5 1 L4.5 1 L5.2 3.4 L4 4.4 Q5 6.8 7.6 8 L8.6 6.8 L11 7.5 L11 9.5 Q10.5 11 9 11 Q1 10 1 3 Q1 1.5 2.5 1 Z" fill="var(--icon-red)"/></svg>
          <span>1 555 4180736</span>
        </li>
        <li class="contact__item">
          <svg class="contact__icon" viewBox="0 0 12 12" aria-hidden="true"><rect x="1" y="2.5" width="10" height="7" fill="none" stroke="var(--icon-red)" stroke-width="1.3"/><path d="M1 2.5 L6 6.5 L11 2.5" fill="none" stroke="var(--icon-red)" stroke-width="1.3"/></svg>
          <span>m.depree@drvventuresinc.example</span>
        </li>
        <li class="contact__item">
          <svg class="contact__icon" viewBox="0 0 12 12" aria-hidden="true"><circle cx="6" cy="6" r="5" fill="none" stroke="var(--icon-red)" stroke-width="1.2"/><ellipse cx="6" cy="6" rx="2.2" ry="5" fill="none" stroke="var(--icon-red)" stroke-width="1"/><path d="M1 6 H11" stroke="var(--icon-red)" stroke-width="1"/></svg>
          <span>www.drvventuresinc.example</span>
        </li>
      </ul>
    </div>
  </section>

</main>
</body>
</html>
```